4th Generation Family Business Needs a New Card Design!

We are a family owned 4th Generation company. We are based in the Sydney, Australia area and we are desperately in need of a more modern and classy card. We are monumental masons who design, supply & erect lasting memorials throughout cemeteries in Sydney. Our customers are normally in a period of grieving. I have attached logo files that will need to be implemented on the card. Company was established 1935. Australian Owned and Operated. Card needs to be designed to PIXO.com specification.

Target Market(s)

Our target market is based upon people that a grieving for family members that have passed away. We also deal with alot of companies that own and operate cemeteries.

Industry/Entity Type

Business

Contact Information for Business Card

Simon Harcourt, Operations Manager, 0417293086, simon@harcourtmemorials.com.au
Lewis Harcourt, Director, 0491630572, lewis@harcourtmemorials.com.au
Phone # 02 9561 3048
Website: www.harcourtmemorials.com.au
Address: Suite 17, 8 Palfrey Lane, West Carlow, Sydney NSW 2156

Font styles to use
Serif
Decorative
Script

Requirements
Must have
• Would like to see the logo nicely implemented with a modern design. Embossed lettering would be a nice additive.

```html
<!DOCTYPE html>
<html lang="en">
<head>
<meta charset="utf-8">
<title>Harcourt Memorials – Business Card</title>
<link rel="stylesheet" href="https://fonts.googleapis.com/css2?family=Cinzel:wght@400;600&family=Open+Sans:wght@400&display=swap">
<style>
  :root {
    --bg: #ece9e4;
    --gold: #ecbd2f;
    --gold-text: #e2b02a;
    --charcoal: #231f20;
    --ink: #1f1b1c;
    --white: #ffffff;
    --muted: #4b4748;
    --address: #3a3637;
  }
  * { box-sizing: border-box; margin: 0; padding: 0; }
  html, body { width: 1200px; height: 900px; overflow: hidden; }
  body { background: var(--bg); position: relative; font-family: "Open Sans", Arial, sans-serif; }

  .card {
    position: absolute;
    width: 540px;
    height: 309px;
    border-radius: 3px;
    overflow: hidden;
    box-shadow: 0 10px 24px rgba(0,0,0,0.18);
  }

  /* Front */
  .card-front { left: 50px; top: 140px; background: var(--gold); }
  .brand-name {
    position: absolute; left: 0; right: 0; top: 110px;
    text-align: center;
    font-family: "Cinzel", Georgia, serif;
    font-weight: 600;
    font-size: 40px;
    letter-spacing: 2px;
    line-height: 1.1;
    color: var(--ink);
  }

  /* Back */
  .card-back { left: 610px; top: 430px; background: var(--charcoal); }
  .card-back .waves { position: absolute; inset: 0; }
  .back-mark {
    position: absolute; right: 22px; top: 22px;
    font-family: "Cinzel", Georgia, serif;
    font-weight: 600;
    font-size: 40px;
    color: var(--muted);
  }
  .contacts { position: absolute; left: 38px; top: 26px; color: var(--white); }
  .person-name {
    font-family: "Cinzel", Georgia, serif;
    font-size: 17px;
    color: var(--gold-text);
    line-height: 22px;
  }
  .person-role { font-size: 13px; line-height: 19px; }
  .line { display: flex; align-items: center; gap: 6px; font-size: 12.5px; line-height: 18px; }
  .line svg { width: 11px; height: 11px; flex: none; }
  .person + .person { margin-top: 8px; }
  .company-lines { margin-top: 10px; }
  .address {
    position: absolute; right: 22px; top: 216px;
    text-align: right;
    font-size: 11.5px;
    line-height: 17px;
    color: var(--address);
  }
</style>
</head>
<body>

<section class="card card-front" aria-label="Card front">
  <div class="brand-name">Harcourt<br>Memorials</div>
</section>

<section class="card card-back" aria-label="Card back">
  <svg class="waves" viewBox="0 0 540 309" preserveAspectRatio="none" aria-hidden="true">
    <path d="M0,232 C150,292 290,220 380,160 C440,122 495,112 540,110 L540,309 L0,309 Z" fill="var(--gold)"/>
    <path d="M0,252 C160,300 300,232 392,170 C450,132 500,122 540,120 L540,309 L0,309 Z" fill="var(--charcoal)"/>
    <path d="M0,262 C160,306 305,242 398,180 C455,142 505,130 540,128 L540,309 L0,309 Z" fill="var(--white)"/>
  </svg>

  <div class="back-mark">Harcourt</div>

  <div class="contacts">
    <div class="person">
      <div class="person-name">Simon Harcourt</div>
      <div class="person-role">Operations Manager</div>
      <div class="line">
        <svg viewBox="0 0 10 10"><rect x="2.5" y="0.5" width="5" height="9" rx="1" fill="none" stroke="var(--gold)" stroke-width="1.2"/></svg>
        0417293086
      </div>
      <div class="line">
        <svg viewBox="0 0 10 10"><rect x="0.5" y="2" width="9" height="6.5" fill="var(--gold)"/><path d="M0.5,2 L5,6 L9.5,2" fill="none" stroke="var(--charcoal)" stroke-width="0.9"/></svg>
        simon@harcourtmemorials.com.au
      </div>
    </div>
    <div class="person">
      <div class="person-name">Lewis Harcourt</div>
      <div class="person-role">Director</div>
      <div class="line">
        <svg viewBox="0 0 10 10"><rect x="2.5" y="0.5" width="5" height="9" rx="1" fill="none" stroke="var(--gold)" stroke-width="1.2"/></svg>
        0491630572
      </div>
      <div class="line">
        <svg viewBox="0 0 10 10"><rect x="0.5" y="2" width="9" height="6.5" fill="var(--gold)"/><path d="M0.5,2 L5,6 L9.5,2" fill="none" stroke="var(--charcoal)" stroke-width="0.9"/></svg>
        lewis@harcourtmemorials.com.au
      </div>
    </div>
    <div class="company-lines">
      <div class="line">
        <svg viewBox="0 0 10 10"><path d="M1,4 C1,1.5 9,1.5 9,4 L7,4.5 L6.5,3.5 L3.5,3.5 L3,4.5 Z" fill="var(--gold)"/><rect x="2" y="5" width="6" height="4" rx="0.8" fill="var(--gold)"/></svg>
        02 9561 3048
      </div>
      <div class="line">
        <svg viewBox="0 0 10 10"><circle cx="5" cy="5" r="4.3" fill="var(--gold)"/><path d="M0.7,5 H9.3 M5,0.7 C2.5,3 2.5,7 5,9.3 M5,0.7 C7.5,3 7.5,7 5,9.3" fill="none" stroke="var(--charcoal)" stroke-width="0.7"/></svg>
        www.harcourtmemorials.com.au
      </div>
    </div>
  </div>

  <div class="address">Suite 17, 8 Palfrey Lane,<br>West Carlow, Sydney NSW 2156</div>
</section>

</body>
</html>
```